Corwin Beacon Lighting - Commercial & Residential Landscape Lighting

Landscape Lighting Services & Design: Create a website for our landscape lighting company. We would like the design to be tailored around this description:
Illuminate with Confidence. Designed with Precision. Installed with Care.
Locally and veteran-owned, we take pride in transforming outdoor spaces through innovative lighting solutions tailored to your vision. From landscape and holiday lighting to permanent installations, our effortless process and expert design deliver breathtaking results and lasting curb appeal. Backed by a lifetime warranty and quarterly service options, our commitment to quality and customer satisfaction is unwavering. Try before you buy and experience your home in a whole new light with our complimentary demo kit — see the stunning effects before you decide.
- Also, add in this information as well; Outdoor Lighting not only beautifies spaces but also significantly enhances safety by illuminating your home or business. Beautifully lit entrances deter potential intruders, making your home a safer place for your loved ones. we also offer quarterly service plans to ensure lighting equipment continues to operate & illuminate effectively throughout the year. Also mention we provide free estimates and we are offering a 10% discount to military, veterans, and first responders.

Target Market(s)

Luxury market

Industry/Entity Type

Landscape Lighting - Residential & Commercial Lighting Services

Coding

Coded - Design and coding required

Number of Pages Required

2 page

Colors
00AB8E
00BBA5
67D7C9
C6EFE9
E9F9F6
59FF00
82FF00
B8FF75
E3FFCB
F4FFEA
FFC000
F8CF3A
FAE287
FDF2CF
FEFAEE

Requirements
Must have
• a lead generation button where people can submit their information for us to reach out to them and schedule their free estimate, homepage, about page, contact page, products and services page, user friendly, easy to navigate, and it also must be engaging and eye popping, as well as appealing to the luxury market. Please use colors; verdent green, dark green, ivory, and sunny yellow. Also, include an about page that references our story; Derek is retired Army and he opened a fitness studio in 2017 with his wife Jolene. He has installed low voltage lighting in every home he lived in and for his friends and family over the years and decided to open his own business because he is passionate about beautifying outdoor landscapes and highlighting a properties full potential, not only in the day but at night as well all while providing safety and security for his clients. Having a deep respect for nature and landscaping, he wants to provide the same care and quality to each of his clients as he has in the fitness industry for decades. He believes small businesses are the back bone of America and he's excited to provide a service that is all to often neglected in the design of a home.
Nice to have
• I would like to have a clear intent and purpose, engaging web design, clear call to action, optimized for search engines, mobile friendy design, security measures, credibility indicators

```html
<!DOCTYPE html>
<html lang="en">
<head>
<meta charset="utf-8">
<title>Corwin Beacon Lighting — Landscape Lighting</title>
<link href="https://fonts.googleapis.com/css2?family=Lato:ital,wght@0,400;0,700;0,900;1,400&family=Poppins:wght@400;500&display=swap" rel="stylesheet">
<style>
:root{
  --night:#1e1a0f;
  --night-2:#15120a;
  --teal:#00AB8E;
  --teal-2:#00BBA5;
  --mint:#C6EFE9;
  --sun:#F8CF3A;
  --gold:#FFC000;
  --ivory:#FEFAEE;
  --ink:#2a2a2a;
  --muted:#555;
  --white:#fff;
}
*{margin:0;padding:0;box-sizing:border-box}
html,body{width:1200px;height:3795px;overflow:hidden}
body{font-family:'Lato',sans-serif;color:var(--ink);background:var(--white);position:relative}
.abs{position:absolute}
.btn{position:absolute;display:flex;align-items:center;justify-content:center;gap:8px;border-radius:30px;font-size:15px;text-transform:uppercase;letter-spacing:.2px}
.btn svg{width:16px;height:16px}
.btn-teal{background:linear-gradient(90deg,var(--teal),var(--teal-2));color:var(--white)}
.btn-sun{background:var(--sun);color:#3a2e08}

/* header */
.site-header{position:absolute;top:0;left:0;width:1200px;height:120px;background:var(--night);border-bottom:1px solid #4a3c14}
.brand{position:absolute;left:108px;top:38px;display:flex;align-items:center;gap:10px;color:var(--sun);font-weight:700;font-size:24px;letter-spacing:1px;white-space:nowrap}
.brand i{width:12px;height:12px;border-radius:50%;background:var(--sun);display:block}
.nav{position:absolute;top:56px;left:376px;display:flex;gap:32px;font-size:15px;color:var(--white);text-transform:uppercase}
.nav .active{color:var(--sun);text-decoration:underline;text-underline-offset:4px}

/* hero */
.hero{position:absolute;top:121px;left:0;width:1200px;height:574px;background:linear-gradient(100deg,#0f120b 0%,#2a2618 40%,#5b3f25 70%,#3a2c1c 100%)}
.hero h1{position:absolute;left:113px;top:128px;color:var(--white);font-weight:900;font-size:38px;line-height:53px;text-transform:uppercase;letter-spacing:-.5px}
.hero h1 span{color:var(--sun)}
.hero p{position:absolute;left:113px;top:298px;width:480px;color:var(--white);font-size:18px;line-height:31px}
.dots{position:absolute;left:579px;top:510px;display:flex;gap:8px;align-items:center}
.dots i{width:7px;height:7px;border-radius:50%;background:var(--white);display:block}
.dots i.on{width:14px;height:14px}

/* sections */
.sec-title{position:absolute;left:0;width:1200px;display:flex;justify-content:center;align-items:center;gap:16px;font-size:30px;font-weight:700;text-transform:uppercase;color:var(--ink)}
.sec-title::before,.sec-title::after{content:"";width:46px;height:3px;background:var(--teal)}
.why{position:absolute;top:695px;left:0;width:1200px;height:540px;background:linear-gradient(#fff,#f7f7f7)}
.center{position:absolute;left:0;width:1200px;text-align:center}
.card{position:absolute;top:977px;width:264px;height:210px;border:1px solid #999;border-radius:12px;background:var(--white);text-align:center;padding:20px 14px 0}
.card svg{width:56px;height:56px;stroke:var(--teal);fill:none;stroke-width:2}
.card h3{font-weight:400;font-size:19px;margin:8px 0 10px;white-space:nowrap}
.card p{font-size:12px;line-height:20px;color:var(--muted);padding:0 14px}
.card.lit{background:linear-gradient(160deg,#2c3a2a,#1a2116 60%,#3a2a14);border-color:#1a2116}
.card.lit h3,.card.lit p{color:var(--white)}
.card.lit svg{stroke:var(--white)}

.offer{position:absolute;left:113px;top:1287px;width:977px;height:399px;border-radius:14px;background:linear-gradient(90deg,#2f2a1c,#3d3a2a 45%,#4a3a1c 75%,#2a2418)}
.offer .t{position:absolute;top:68px;left:0;width:977px;display:flex;justify-content:center;align-items:center;gap:16px;color:var(--white);font-weight:700;font-size:30px}
.offer .t::before,.offer .t::after{content:"";width:64px;height:2px;background:var(--white)}

.proj-title{position:absolute;left:111px;top:1790px;font-size:30px;font-weight:700;color:#333;display:flex;align-items:center;gap:10px}
.proj-title::after{content:"";width:46px;height:3px;background:var(--teal);margin-top:-20px}
.arrow-btn{position:absolute;top:1870px;width:38px;height:38px;border-radius:50%;border:2px solid #222;display:flex;align-items:center;justify-content:center}
.arrow-btn.on{border-color:var(--teal);width:46px;height:46px;top:1866px}
.photo{position:absolute;top:1975px;width:320px;height:314px;border-radius:10px}

.services{position:absolute;top:2383px;left:0;width:1200px;height:460px;background:linear-gradient(100deg,#1e3326,#2b3c3a 40%,#3a3a48 70%,#4a3a2a)}
.services .sec-title{color:var(--white);top:75px}
.services .sec-title::before,.services .sec-title::after{background:var(--white)}
.svc{position:absolute;top:2567px;width:204px;height:150px;background:var(--white);border-radius:10px;text-align:center;display:flex;flex-direction:column;align-items:center;justify-content:center;gap:6px;font-size:19px;line-height:24px;color:#333}
.svc svg{width:50px;height:50px;stroke:var(--teal);fill:none;stroke-width:2}

.ready{position:absolute;top:2780px;left:0;width:1200px;height:580px}
.ready h2{position:absolute;left:598px;top:120px;font-size:30px;line-height:42px;font-weight:700;color:#333;text-transform:uppercase}
.ready h2 .rule::after{content:"";display:inline-block;width:46px;height:3px;background:var(--teal);margin-left:10px;vertical-align:middle}

/* footer */
.site-footer{position:absolute;top:3350px;left:0;width:1200px;height:445px;background:var(--night)}
.contact{position:absolute;top:75px;display:flex;gap:14px;color:var(--white);font-family:'Poppins',sans-serif;font-size:15px;line-height:24px}
.contact b{font-weight:500;font-size:14px}
.contact svg{width:28px;height:28px;fill:var(--gold);margin-top:6px}
.col{position:absolute;top:177px;font-family:'Poppins',sans-serif;color:var(--white);font-size:15px}
.col h4{color:var(--gold);font-weight:500;font-size:16px;margin-bottom:6px}
.col li{list-style:none;line-height:31.5px;display:flex;align-items:center;gap:10px}
.col li svg{width:12px;height:12px;stroke:var(--gold);stroke-width:2;fill:none}
.foot-bottom{position:absolute;top:3745px;left:0;width:1200px;border-top:1px solid #c8a33a;height:50px;font-family:'Poppins',sans-serif;font-size:13px;color:var(--white)}
</style>
</head>
<body>

<header class="site-header">
  <div class="brand"><i></i>CORWIN BEACON</div>
  <nav class="nav">
    <span class="active">Home</span><span>About</span><span>Products &amp; Services</span><span>Contact</span>
  </nav>
  <a class="btn btn-teal" style="left:857px;top:44px;width:233px;height:46px">Get a Free Estimate
    <svg viewBox="0 0 16 16" fill="none" stroke="currentColor" stroke-width="2"><path d="M2 8h11M9 4l4 4-4 4"/></svg></a>
</header>

<section class="hero" role="img" aria-label="Brick home with landscape lighting at dusk">
  <h1>Illuminate with <span>Confidence.</span><br>Designed with <span>Precision.</span><br>Installed with <span>Care.</span></h1>
  <p>Transform your outdoor space with professional lighting solutions that blend beauty, safety, and innovation.</p>
  <a class="btn btn-sun" style="left:113px;top:385px;width:236px;height:47px">Get a Free Estimate
    <svg viewBox="0 0 16 16" fill="none" stroke="currentColor" stroke-width="2"><path d="M2 8h11M9 4l4 4-4 4"/></svg></a>
  <div class="dots"><i></i><i class="on"></i><i></i></div>
</section>

<section class="why">
  <h2 class="sec-title" style="top:80px">Why Choose Us</h2>
  <p class="center" style="top:140px;font-size:17px;color:#333">Veteran-Owned. Locally Trusted. Designed for Distinction.</p>
  <p class="center" style="top:172px;font-size:14px;line-height:25px;color:#333;padding:0 180px">Locally and veteran-owned, we take pride in transforming outdoor spaces through innovative lighting solutions tailored to your vision. From landscape and holiday lighting to permanent installations, our effortless process and expert design deliver breathtaking results and lasting curb appeal.</p>
</section>

<div class="card" style="left:34px">
  <svg viewBox="0 0 56 56"><circle cx="28" cy="28" r="18"/><circle cx="28" cy="28" r="8"/><path d="M28 4v14M28 38v14M4 28h14M38 28h14"/></svg>
  <h3>Precision Installation</h3>
  <p>We treat every property as our own. Our expert team ensures seamless, low-voltage installation with</p>
</div>
<div class="card lit" style="left:322px" role="img" aria-label="Evening lit garden behind card text">
  <svg viewBox="0 0 56 56"><circle cx="20" cy="14" r="6"/><circle cx="36" cy="14" r="6"/><path d="M8 40c0-10 6-16 12-16M48 40c0-10-6-16-12-16"/><path d="M28 30l10 4v8c0 6-10 10-10 10s-10-4-10-10v-8z"/></svg>
  <h3>Veteran &amp; Family-Owned</h3>
  <p>Built on discipline, service, and integrity, our company is proudly led by a U.S. veteran into every design.</p>
</div>
<div class="card" style="left:612px">
  <svg viewBox="0 0 56 56"><rect x="20" y="6" width="30" height="22" rx="2"/><path d="M28 20l7-6 7 6M30 20v6h10v-6"/><circle cx="14" cy="32" r="6"/><path d="M4 52c0-8 4-12 10-12s10 4 10 12M24 44h24"/></svg>
  <h3>Complimentary Demo Kit</h3>
  <p>Experience your home in a new light before you commit. Our free demo kit lets you visualize the involved.</p>
</div>
<div class="card" style="left:901px">
  <svg viewBox="0 0 56 56"><path d="M26 4l18 6v14c0 14-18 24-18 24S8 38 8 24V10z"/><rect x="18" y="16" width="16" height="14"/><circle cx="42" cy="44" r="8"/><path d="M42 40v4h3"/></svg>
  <h3>Lifetime Warranty</h3>
  <p>We stand by our craftsmanship. All lighting systems come backed with a lifetime warranty, because quality</p>
</div>

<section class="offer" role="img" aria-label="Technician installing path lights in a garden at dusk">
  <h2 class="t">SPECIAL OFFERS</h2>
  <p class="center" style="top:122px;width:977px;color:var(--white);font-size:20px">
    <svg viewBox="0 0 20 20" width="22" height="22" style="vertical-align:-3px;margin-right:6px"><path fill="var(--gold)" d="M10 1l2.6 5.6 6 .7-4.5 4.1 1.2 6L10 14.4 4.7 17.4l1.2-6L1.4 7.3l6-.7z"/></svg>Proud to Serve Those Who Serve</p>
  <p class="center" style="top:170px;width:977px;color:var(--white);font-size:28px;line-height:40px">We offer <b style="color:var(--sun)">10% off</b> for military, veterans, and<br>first responders.</p>
  <a class="btn btn-sun" style="left:370px;top:283px;width:234px;height:45px">Claim Your Discount</a>
</section>

<h2 class="proj-title">FEATURED PROJECTS</h2>
<p class="abs" style="left:111px;top:1842px;font-size:19px;color:#333">See the Transformation. Experience the Glow.</p>
<p class="abs" style="left:111px;top:1881px;width:800px;font-size:14px;line-height:25px;color:#333">Our lighting designs don’t just illuminate — they <b>elevate</b>. Explore a selection of beautifully lit homes, patios, pathways, and landscapes that show what’s possible when expertise meets artistry.</p>
<span class="arrow-btn on" style="left:990px"><svg width="20" height="20" viewBox="0 0 16 16" fill="none" stroke="#00AB8E" stroke-width="2"><path d="M14 8H3M7 4L3 8l4 4"/></svg></span>
<span class="arrow-btn" style="left:1050px"><svg width="18" height="18" viewBox="0 0 16 16" fill="none" stroke="#222" stroke-width="2"><path d="M2 8h11M9 4l4 4-4 4"/></svg></span>
<div class="photo" style="left:107px;background:linear-gradient(160deg,#3a4660,#6a6a70 50%,#2f3a22)" role="img" aria-label="Modern two-story home with uplit walls and palms"></div>
<div class="photo" style="left:439px;background:linear-gradient(170deg,#5a5550,#8a6a3a 40%,#3a2e22 80%)" role="img" aria-label="Aerial view of a glowing pergola patio at night">
  <div class="abs" style="left:15px;top:14px;width:290px;height:284px;border:3px solid var(--sun);border-radius:10px"></div>
</div>
<div class="photo" style="left:770px;background:linear-gradient(170deg,#2a3040,#4a3a2a 45%,#3a5a2a 70%,#8a3a4a)" role="img" aria-label="Home garden with lit flower beds and curved path"></div>

<section class="services" role="img" aria-label="Stone house and flower garden lit at night">
  <h2 class="sec-title">Our Services</h2>
  <p class="center" style="top:118px;color:var(--white);font-size:20px">Transform Your Outdoors with Custom Lighting Solutions</p>
</section>
<div class="svc" style="left:75px"><svg viewBox="0 0 50 50"><rect x="6" y="20" width="22" height="20"/><path d="M4 20h26M32 8h10v32H32M2 44h46"/></svg>Landscape Lighting</div>
<div class="svc" style="left:288px"><svg viewBox="0 0 50 50"><path d="M4 10c10 8 32 8 42 0"/><path d="M14 14l-4 14 6 8 6-8-2-12M34 14l4 14-6 8-6-8 2-12"/></svg>Holiday &amp; Event<br>Lighting</div>
<div class="svc" style="left:499px"><svg viewBox="0 0 50 50"><rect x="20" y="6" width="10" height="10"/><path d="M25 16v26M10 42h30M14 36l22-6M6 4l8 6M44 4l-8 6"/></svg>Security &amp; Safety<br>Lighting</div>
<div class="svc" style="left:711px"><svg viewBox="0 0 50 50"><circle cx="18" cy="14" r="8"/><path d="M4 46c0-12 6-18 14-18s14 6 14 18M30 24h16v14H30z"/></svg>Maintenance &amp;<br>Service Plans</div>
<div class="svc" style="left:923px"><svg viewBox="0 0 50 50"><path d="M25 6v38M14 16h22M10 16a4 4 0 0 0 8 0M32 16a4 4 0 0 0 8 0M14 44h22"/></svg>Permanent Outdoor<br>Installations</div>

<section class="ready">
  <svg class="abs" style="left:0;top:0" width="1200" height="580" viewBox="0 0 1200 580">
    <path d="M0 0 C300 30 500 40 560 40 L1200 40 L1200 580 L0 580Z" fill="#fff"/>
    <path d="M0 560 C400 540 800 560 1200 540 L1200 552 C800 572 400 552 0 572Z" fill="var(--gold)"/>
  </svg>
  <div class="abs" style="left:0;top:22px;width:555px;height:540px;clip-path:polygon(0 0,100% 8%,100% 100%,0 100%);background:linear-gradient(160deg,#6a4a2a,#c08a4a 35%,#5a5a6a 60%,#3a6a2a 85%)" role="img" aria-label="Patio with lantern path light and lavender at dusk"></div>
  <h2><span style="display:block">Ready to Transform Your</span><span class="rule">Outdoors?</span></h2>
  <p class="abs" style="left:597px;top:222px;font-size:19px;font-weight:700;color:#333">Experience Your Home in a Whole New Light</p>
  <p class="abs" style="left:598px;top:268px;width:485px;font-size:15px;line-height:26px;color:#444">Outdoor Lighting not only beautifies spaces but also significantly enhances safety by illuminating your home or business. Beautifully lit entrances deter potential intruders, making your home a safer place for your loved ones. we also offer quarterly service plans to ensure lighting equipment continues to operate &amp; illuminate effectively throughout the year.</p>
  <a class="btn btn-teal" style="left:597px;top:453px;width:232px;height:47px">Get a Free Estimate
    <svg viewBox="0 0 16 16" fill="none" stroke="currentColor" stroke-width="2"><path d="M2 8h11M9 4l4 4-4 4"/></svg></a>
</section>

<footer class="site-footer">
  <div class="brand" style="left:113px;top:82px;font-size:22px"><i></i>CORWIN BEACON</div>
  <div class="contact" style="left:380px"><svg viewBox="0 0 24 24"><path d="M12 2a7 7 0 0 0-7 7c0 5 7 13 7 13s7-8 7-13a7 7 0 0 0-7-7zm0 9.5A2.5 2.5 0 1 1 12 6.5a2.5 2.5 0 0 1 0 5z"/></svg><div>Location<br><b>Ashford Hills, TX</b></div></div>
  <div class="contact" style="left:612px"><svg viewBox="0 0 24 24"><path d="M2 5h20v14H2z" fill="var(--gold)"/><path d="M2 5l10 8 10-8" stroke="#1e1a0f" stroke-width="2" fill="none"/></svg><div>Mail<br><b>info@corwinbeacon.com</b></div></div>
  <div class="contact" style="left:925px"><svg viewBox="0 0 24 24"><path d="M6.6 10.8a15 15 0 0 0 6.6 6.6l2.2-2.2a1 1 0 0 1 1-.25 11 11 0 0 0 3.6.6 1 1 0 0 1 1 1V20a1 1 0 0 1-1 1A17 17 0 0 1 3 4a1 1 0 0 1 1-1h3.5a1 1 0 0 1 1 1 11 11 0 0 0 .6 3.6 1 1 0 0 1-.25 1z"/></svg><div>Call Us<br><b>972.555.0148</b></div></div>

  <div class="col" style="left:113px">
    <h4>About</h4>
    <ul><li>Corwin Beacon Lighting</li><li>Commercial &amp; Residential Landscape Lighting</li><li>Veteran-Owned | Based in Ashford Hills, Texas</li><li>Licensed &amp; Insured | Lifetime Warranty | Free</li><li>Proudly Veteran-Owned &amp; Operated</li></ul>
  </div>
  <div class="col" style="left:538px;font-size:14px">
    <h4>Quick Links</h4>
    <ul><li><svg viewBox="0 0 12 12"><path d="M2 10L10 2M4 2h6v6"/></svg>Home</li><li><svg viewBox="0 0 12 12"><path d="M2 10L10 2M4 2h6v6"/></svg>About</li><li><svg viewBox="0 0 12 12"><path d="M2 10L10 2M4 2h6v6"/></svg>Products &amp; Services</li><li><svg viewBox="0 0 12 12"><path d="M2 10L10 2M4 2h6v6"/></svg>Contact</li><li><svg viewBox="0 0 12 12"><path d="M2 10L10 2M4 2h6v6"/></svg>Request a Free Estimate</li></ul>
  </div>
  <div class="col" style="left:844px;font-size:14px">
    <h4>Services</h4>
    <ul><li><svg viewBox="0 0 12 12"><path d="M2 10L10 2M4 2h6v6"/></svg>Landscape Lighting</li><li><svg viewBox="0 0 12 12"><path d="M2 10L10 2M4 2h6v6"/></svg>Holiday &amp; Event Lighting</li><li><svg viewBox="0 0 12 12"><path d="M2 10L10 2M4 2h6v6"/></svg>Permanent Installations</li><li><svg viewBox="0 0 12 12"><path d="M2 10L10 2M4 2h6v6"/></svg>Security &amp; Safety Lighting</li><li><svg viewBox="0 0 12 12"><path d="M2 10L10 2M4 2h6v6"/></svg>Quarterly Maintenance Plans</li></ul>
  </div>
</footer>
<div class="foot-bottom">
  <span class="abs" style="left:116px;top:20px">© 2025 Corwin Beacon Lighting. All rights reserved.</span>
  <span class="abs" style="left:700px;top:20px;font-style:italic">10% Discount for Military, Veterans &amp; First Responders</span>
</div>

</body>
</html>
```